SaaS Early tech startup business card design

Unique design for experience ecommerce platform company. the business cards will be used by executive members. conformance with color code is required.

```html
<!DOCTYPE html>
<html lang="en">
<head>
<meta charset="utf-8">
<title>Veloa Business Card</title>
<link rel="stylesheet" href="https://fonts.googleapis.com/css2?family=Open+Sans:wght@400;600;700&display=swap">
<style>
  :root {
    --backdrop: #1f1f1f;
    --card: #ffffff;
    --brand-blue: #176590;
    --brand-teal: #12b59a;
    --ink: #222222;
  }
  * { margin: 0; padding: 0; box-sizing: border-box; }
  html, body {
    width: 1200px; height: 988px; overflow: hidden;
    background: var(--backdrop);
    font-family: "Open Sans", Arial, sans-serif;
  }
  .stage {
    width: 1200px; height: 988px;
    display: flex; flex-direction: column;
    align-items: center; justify-content: center; gap: 56px;
  }
  .card {
    position: relative;
    width: 720px; height: 412px;
    background: var(--card);
    border-radius: 22px;
    overflow: hidden;
  }
  .wordmark {
    color: var(--brand-blue);
    font-weight: 700;
    letter-spacing: -1px;
    line-height: 1;
  }
  .card-front .wordmark {
    position: absolute; left: 0; right: 0; top: 140px;
    text-align: center; font-size: 118px;
  }
  .card-back .wordmark {
    position: absolute; left: 268px; top: 86px;
    font-size: 78px;
  }
  .identity {
    position: absolute; right: 378px; top: 222px;
    text-align: right;
  }
  .identity-name {
    color: var(--brand-blue); font-weight: 700; font-size: 26px; line-height: 1.1;
  }
  .identity-role {
    color: var(--ink); font-size: 14px; margin-top: 2px;
  }
  .divider {
    position: absolute; left: 362px; top: 206px;
    width: 2px; height: 76px; background: var(--brand-teal);
  }
  .contacts {
    position: absolute; left: 382px; top: 206px;
    list-style: none;
  }
  .contacts li {
    display: flex; align-items: center; gap: 9px;
    font-size: 15px; color: var(--ink); height: 25px;
  }
  .contacts svg { width: 13px; height: 13px; fill: var(--brand-blue); flex: none; }
  .band {
    position: absolute; left: 0; top: 330px; width: 720px; height: 34px;
  }
  .band-address {
    position: absolute; left: 222px; top: 330px; width: 380px; height: 34px;
    display: flex; align-items: center; justify-content: center;
    color: #ffffff; font-size: 14px; font-weight: 600;
  }
</style>
</head>
<body>
<main class="stage">
  <section class="card card-front" aria-label="Card front">
    <div class="wordmark">Veloa</div>
  </section>

  <section class="card card-back" aria-label="Card back">
    <div class="wordmark">Veloa</div>

    <div class="identity">
      <div class="identity-name">Dana Whitfield</div>
      <div class="identity-role">Managing Director</div>
    </div>

    <div class="divider"></div>

    <ul class="contacts">
      <li>
        <svg viewBox="0 0 16 16" aria-hidden="true"><path d="M3.2 1.5l2.4 2.6-1.3 1.8c.9 2 2.5 3.6 4.6 4.6l1.8-1.3 2.6 2.4-1.5 2.4C6.6 14.2 1.8 9.4 1 3z"/></svg>
        +01 555 0142
      </li>
      <li>
        <svg viewBox="0 0 16 16" aria-hidden="true"><path d="M1 3h14v10H1zM2 4l6 5 6-5v-.2H2z" fill-rule="evenodd"/></svg>
        hello@veloa.io
      </li>
      <li>
        <svg viewBox="0 0 16 16" aria-hidden="true"><circle cx="8" cy="8" r="7"/></svg>
        www.veloa.io
      </li>
    </ul>

    <svg class="band" viewBox="0 0 720 34" aria-hidden="true">
      <polygon points="0,0 214,0 206,34 0,34" fill="var(--brand-teal)"/>
      <polygon points="222,0 606,0 598,34 214,34" fill="var(--brand-blue)"/>
      <polygon points="614,0 720,0 720,34 606,34" fill="var(--brand-teal)"/>
    </svg>
    <div class="band-address">18 Harbor Lane, Springfield, Country - 40217</div>
  </section>
</main>
</body>
</html>
```